Corvane Holdings , new business card design

investment firm with corporate clients . need double sided business card , vertical and horizontal options ,logo must be clear. prefer pantone colors only and sharp design. website also www.corvane.ae

Khalid Bin Tarrafi
Managing Director
Tel. +971 4 387 2940
Mobile +971 50 518 2403
khalid@corvane.ae
Q-Span Plaza, officw 18-B07, Warqa Gardens, Dubai

Contact Information for Business Card

Khalid Bin Tarrafi
Managing Director

Font styles to use
Serif

Colors

Designer to choose colors to be used in the design.

```html
<!DOCTYPE html>
<html lang="en">
<head>
<meta charset="utf-8">
<title>Corvane Holdings — Business Card</title>
<link rel="stylesheet" href="https://fonts.googleapis.com/css2?family=Roboto:wght@300;400&family=Roboto+Condensed:wght@400;700&display=swap">
<style>
  :root {
    --backdrop: #e4e4e4;
    --paper: #f4f4f4;
    --ink: #111216;
    --band-dark: #0b0b0e;
    --steel-blue: #436f96;
    --rule: #9a9a9a;
    --white: #ffffff;
    --muted: #555;
  }
  * { margin: 0; padding: 0; box-sizing: border-box; }
  html, body { width: 1200px; height: 960px; overflow: hidden; }
  body {
    background: var(--backdrop);
    position: relative;
    font-family: "Roboto", Arial, sans-serif;
  }
  .card {
    position: absolute;
    background: var(--paper);
    overflow: hidden;
  }
  .card--front { left: 314px; top: 113px; width: 602px; height: 344px; }
  .card--back  { left: 311px; top: 472px; width: 600px; height: 343px; }

  .wordmark {
    position: absolute;
    left: 0; right: 0;
    text-align: center;
    color: var(--ink);
    font-family: "Roboto", Arial, sans-serif;
    font-weight: 300;
    line-height: 1;
  }
  .wordmark__name { display: block; font-size: 46px; letter-spacing: 0.34em; padding-left: 0.34em; }
  .wordmark__sub  { display: block; font-size: 15px; letter-spacing: 0.72em; padding-left: 0.72em; margin-top: 12px; }
  .card--front .wordmark { top: 58px; }
  .card--back .wordmark  { top: 135px; }

  .contact-band {
    position: absolute;
    left: 0; top: 180px; width: 100%; height: 131px;
    background: var(--band-dark);
    color: var(--white);
    text-align: center;
  }
  .contact-band__name {
    font-family: "Roboto Condensed", "Arial Narrow", sans-serif;
    font-weight: 700;
    font-size: 21px;
    color: var(--steel-blue);
    margin-top: 20px;
    letter-spacing: 0.01em;
  }
  .contact-band__title {
    display: flex; align-items: center; justify-content: center; gap: 6px;
    font-family: "Roboto Condensed", "Arial Narrow", sans-serif;
    font-size: 15px;
    letter-spacing: 0.04em;
    margin-top: 2px;
  }
  .contact-band__title::before,
  .contact-band__title::after {
    content: ""; width: 107px; height: 1px; background: var(--rule);
  }
  .contact-band__address { font-size: 14px; margin-top: 12px; }
  .contact-band__lines {
    display: flex; justify-content: center; align-items: center; gap: 4px;
    font-size: 14px; margin-top: 6px;
  }
  .contact-band__lines svg { width: 13px; height: 13px; fill: var(--steel-blue); }
  .contact-band__lines .item { display: inline-flex; align-items: center; gap: 3px; margin-right: 2px; }

  .web-band {
    position: absolute;
    left: 0; top: 314px; width: 100%; height: 30px;
    background: var(--steel-blue);
    color: var(--white);
    font-size: 14px;
    letter-spacing: 0.62em;
    padding-left: 0.62em;
    text-align: center;
    line-height: 30px;
  }
  .web-line {
    position: absolute;
    left: 0; right: 0; top: 289px;
    text-align: center;
    color: var(--muted);
    font-size: 14px;
    letter-spacing: 0.62em;
    padding-left: 0.62em;
  }
</style>
</head>
<body>
  <section class="card card--front" aria-label="Business card front">
    <div class="wordmark">
      <span class="wordmark__name">CORVANE</span>
      <span class="wordmark__sub">HOLDINGS</span>
    </div>
    <div class="contact-band">
      <p class="contact-band__name">KHALID BIN TARRAFI</p>
      <p class="contact-band__title">MANAGING DIRECTOR</p>
      <p class="contact-band__address">Q-Span Plaza, officw 18-B07, Warqa Gardens, Dubai</p>
      <p class="contact-band__lines">
        <span class="item">
          <svg viewBox="0 0 24 24" aria-hidden="true"><path d="M6.6 10.8a15.1 15.1 0 0 0 6.6 6.6l2.2-2.2a1 1 0 0 1 1-.25 11.4 11.4 0 0 0 3.6.57 1 1 0 0 1 1 1V20a1 1 0 0 1-1 1A17 17 0 0 1 3 4a1 1 0 0 1 1-1h3.5a1 1 0 0 1 1 1c0 1.25.2 2.45.57 3.57a1 1 0 0 1-.25 1z"/></svg>
          +971 4 387 2940
        </span>
        <span class="item">
          <svg viewBox="0 0 24 24" aria-hidden="true"><path d="M7 1h10a2 2 0 0 1 2 2v18a2 2 0 0 1-2 2H7a2 2 0 0 1-2-2V3a2 2 0 0 1 2-2zm0 3v15h10V4z"/></svg>
          +971 50 518 2403
        </span>
        <span class="item">
          <svg viewBox="0 0 24 24" aria-hidden="true"><path d="M2 5h20v14H2zm2 2v.5l8 5 8-5V7z"/></svg>
          khalid@corvane.ae
        </span>
      </p>
    </div>
    <div class="web-band">www.corvane.ae</div>
  </section>

  <section class="card card--back" aria-label="Business card back">
    <div class="wordmark">
      <span class="wordmark__name">CORVANE</span>
      <span class="wordmark__sub">HOLDINGS</span>
    </div>
    <p class="web-line">www.corvane.ae</p>
  </section>
</body>
</html>
```